Animal Horse & Bedding Company Needs a Website Coded & Designed

We need a website for a new animal bedding and feed company that is visually grabbing and vibrant. We would like to see a website that displays trust, quality and confidence. Needs to be responsive and mobile friendly for all browsers and coded for both Android & IOS. SEO is also important.

Joomla or Wordpress – must be both desktop and mobile friendly with fast page load speed. Need the ability to edit ourselves in Wordpress or Joomla.

Full details attached below with some layout and content ideas.

Coding

Coded - Design and coding required

Number of Pages Required

5+ page

Font styles to use
Sans Serif

Requirements
Must have
• Needs to be responsive and mobile friendly for all browsers and coded for both Android & IOS. SEO is also important.

Wordpress – must be both desktop and mobile friendly with fast page load speed. Need the ability to edit ourselves in Wordpress.

Logo Colours:
Dark Brown
CMYK: 50 / 70 / 80 / 70
Pantone: 4625C

Orange
CMYK: 0 / 50 / 100 / 0
Pantone: 144C
Nice to have
• Use picture of building attached and super impose logo on building.

```html
<!DOCTYPE html>
<html lang="en">
<head>
<meta charset="utf-8">
<title>Hayfield Crest – Bedding &amp; Feed</title>
<link href="https://fonts.googleapis.com/css2?family=Oswald:wght@300;400;500&family=Montserrat:wght@400;500;600;700&display=swap" rel="stylesheet">
<style>
:root{
  --brown:#3b1d10;
  --brown-deep:#3a1c0e;
  --orange:#f7941d;
  --orange-soft:#fbb040;
  --cream:#f8f4ee;
  --text:#4a3a30;
  --muted:#6b5d55;
  --white:#ffffff;
}
*{margin:0;padding:0;box-sizing:border-box}
html,body{width:1200px;height:3968px;overflow:hidden;background:var(--white)}
body{position:relative;font-family:"Montserrat",sans-serif;color:var(--text)}
.abs{position:absolute}

/* header */
.site-header{left:0;top:0;width:1200px;height:96px;background:var(--white)}
.brand{left:72px;top:18px;display:flex;align-items:center;gap:12px}
.brand-dot{width:44px;height:44px;border-radius:50%;background:var(--orange)}
.brand-name{font-family:"Oswald",sans-serif;font-weight:400;color:var(--brown);font-size:30px;line-height:1;letter-spacing:2px;white-space:nowrap}
.brand-sub{font-family:"Oswald",sans-serif;font-weight:400;color:var(--brown);font-size:11px;letter-spacing:8px;margin-top:4px;white-space:nowrap}
.nav{left:412px;top:36px;display:flex;font-size:14px;font-weight:500;color:var(--brown);white-space:nowrap}
.nav a{text-decoration:none;color:inherit;margin-right:54px}
.nav a.active{color:var(--orange)}
.quote-btn{left:962px;top:30px;width:155px;height:40px;border-radius:20px;background:var(--brown);color:var(--white);font-size:12px;font-weight:700;display:flex;align-items:center;justify-content:center}

/* hero */
.hero{left:0;top:96px;width:1200px;height:640px}
.hero-title{left:62px;top:288px;color:var(--white);font-family:"Oswald",sans-serif;font-weight:400;font-size:90px;letter-spacing:3px;line-height:1;white-space:nowrap}
.hero-sub{left:158px;top:386px;color:var(--white);font-family:"Oswald",sans-serif;font-weight:300;font-size:36px;letter-spacing:10px;white-space:nowrap}
.learn-btn{left:214px;top:444px;width:182px;height:52px;border-radius:26px 0 26px 0;background:var(--orange);color:var(--white);font-weight:700;font-size:15px;display:flex;align-items:center;justify-content:center;box-shadow:4px 4px 0 #e07a10}
.dots{left:570px;top:666px;display:flex;gap:9px}
.dots span{width:11px;height:11px;border-radius:50%;background:var(--white)}
.dots span.on{background:var(--orange)}

/* intro cards */
.card{top:790px;width:320px;height:408px;overflow:hidden}
.card .photo{width:320px;height:210px}
.card h3{font-family:"Oswald",sans-serif;font-weight:400;font-size:25px;text-align:center;margin-top:24px;letter-spacing:.5px;white-space:nowrap}
.card h3::after{content:"";display:block;width:42px;height:2px;background:currentColor;margin:8px auto 0;opacity:.8}
.card p{font-size:10.5px;line-height:17px;text-align:center;padding:16px 40px 0}
.card-light{left:108px;background:var(--white);box-shadow:0 2px 6px rgba(0,0,0,.12);color:var(--brown)}
.card-light p{color:var(--muted)}
.card-orange{left:445px;background:var(--orange);color:var(--white)}
.card-orange h3::after{background:var(--white)}
.card-brown{left:781px;background:var(--brown);color:var(--white)}
.card-brown h3::after{background:var(--orange)}

/* benefits band */
.benefits{left:0;top:1250px;width:1200px;height:240px;background:var(--cream)}
.benefit{top:82px;display:flex;gap:14px}
.benefit h4{font-size:17px;font-weight:600;color:var(--brown);line-height:22px;letter-spacing:.5px}
.benefit p{font-size:11px;color:var(--muted);line-height:20px;margin-top:10px}
.divider{top:95px;width:1px;height:110px;background:#ddd3c6}

/* bedding */
.section-title{font-family:"Oswald",sans-serif;font-weight:400;color:var(--brown);font-size:44px;letter-spacing:2px;text-align:center}
.section-title::after{content:"";display:block;width:50px;height:3px;background:var(--orange);margin:6px auto 0}
.bed-title{left:0;top:1565px;width:1200px}
.bed-photo{left:424px;top:1659px;width:360px;height:360px;border-radius:50%}
.badge{width:76px;height:76px;border-radius:50%;display:flex;align-items:center;justify-content:center}
.badge.o{background:var(--orange)}
.badge.b{background:var(--brown)}
.bed-label{font-size:14px;font-weight:500;color:var(--brown);line-height:19px}
.view-btn{height:52px;background:var(--brown);color:var(--white);font-size:14px;font-weight:700;display:flex;align-items:center;justify-content:center;border-radius:26px 0 26px 0}

/* feed */
.feed{left:0;top:2390px;width:1200px;height:625px}
.feed-title{left:118px;top:2490px;color:var(--white);font-family:"Oswald",sans-serif;font-weight:400;font-size:44px;letter-spacing:2px}
.feed-title::after{content:"";display:block;width:50px;height:3px;background:var(--white);margin-top:4px}
.feed-copy{left:120px;top:2564px;width:520px;color:var(--white);font-size:11.5px;line-height:20px}
.feed-item{display:flex;align-items:center;gap:8px;color:var(--white);font-size:10px;font-weight:700;line-height:12px}
.feed-photo-a{left:696px;top:2492px;width:403px;height:343px}
.feed-photo-b{left:620px;top:2721px;width:221px;height:189px}

/* delivery */
.map{left:135px;top:3100px;width:472px;height:380px}
.deliv-title{left:654px;top:3160px;color:var(--brown);font-family:"Oswald",sans-serif;font-weight:400;font-size:38px;letter-spacing:1.5px;white-space:nowrap}
.deliv-title::after{content:"";display:block;width:50px;height:3px;background:var(--orange);margin-top:10px}
.deliv-copy{left:660px;top:3244px;width:430px;font-size:12px;line-height:22px;color:var(--muted)}
.deliv-copy p+p{margin-top:6px}
.outline-btn{left:638px;top:3358px;width:154px;height:46px;border:2px solid var(--orange);border-radius:23px 0 23px 0;color:var(--orange);font-size:12px;font-weight:700;display:flex;align-items:center;justify-content:center}

/* footer */
.footer{left:0;top:3470px;width:1200px;height:498px}
.foot-brand{left:96px;top:3640px;text-align:center;width:280px}
.foot-dot{width:46px;height:46px;border-radius:50%;background:var(--orange);margin:0 auto 10px}
.foot-name{font-family:"Oswald",sans-serif;font-weight:400;color:var(--orange);font-size:34px;letter-spacing:2px;line-height:1;white-space:nowrap}
.foot-sub{font-family:"Oswald",sans-serif;color:var(--orange);font-size:12px;letter-spacing:9px;margin-top:4px;line-height:14px;white-space:nowrap}
.socials{left:167px;top:3770px;display:flex;gap:6px}
.socials span{width:32px;height:32px;border-radius:50%;background:var(--orange)}
.socials span+span{background:var(--white)}
.foot-col h5{color:var(--white);font-size:14px;font-weight:500;letter-spacing:.5px;margin-bottom:16px;white-space:nowrap}
.foot-col li{list-style:none;color:#e8dcd2;font-size:11px;line-height:26px}
.contact-line{display:flex;gap:10px;color:#e8dcd2;font-size:10px;line-height:25px}
.email-field{left:864px;top:3668px;width:231px;height:36px;border:1px solid #b8a598;border-radius:18px;color:#d9ccc2;font-size:10px;padding:11px 20px}
.sub-btn{left:870px;top:3718px;width:132px;height:34px;border-radius:17px;background:var(--orange);color:var(--white);font-size:10px;font-weight:700;display:flex;align-items:center;justify-content:center}
.copyright{left:0;top:3918px;width:1200px;text-align:center;color:#cbbcb0;font-size:9.5px}
</style>
</head>
<body>

<!-- header -->
<header class="abs site-header">
  <div class="abs brand">
    <div class="brand-dot"></div>
    <div>
      <div class="brand-name">HAYFIELD CREST</div>
      <div class="brand-sub">BEDDING &amp; FEED</div>
    </div>
  </div>
  <nav class="abs nav">
    <a class="active">HOME</a><a>ABOUT</a><a>FEED</a><a>BEDDING</a><a>CONTACT US</a>
  </nav>
  <div class="abs quote-btn">REQUEST QUOTE &nbsp;›</div>
</header>

<!-- hero -->
<section class="abs hero">
  <svg width="1200" height="640" viewBox="0 0 1200 640">
    <defs>
      <linearGradient id="heroSky" x1="0" y1="0" x2="0" y2="1">
        <stop offset="0" stop-color="#5d6a3a"/>
        <stop offset=".5" stop-color="#8a8a4e"/>
        <stop offset="1" stop-color="#b59a62"/>
      </linearGradient>
      <radialGradient id="heroHorse" cx=".68" cy=".42" r=".35">
        <stop offset="0" stop-color="#9a4a1c"/>
        <stop offset="1" stop-color="#9a4a1c" stop-opacity="0"/>
      </radialGradient>
    </defs>
    <g role="img" aria-label="Chestnut horse standing in a sunny meadow">
      <rect width="1200" height="640" fill="url(#heroSky)"/>
      <rect width="1200" height="640" fill="url(#heroHorse)"/>
    </g>
    <path d="M0 540 Q600 700 1200 540 L1200 640 L0 640 Z" fill="#ffffff"/>
    <path d="M0 540 Q600 700 1200 540" fill="none" stroke="#f7941d" stroke-width="6" transform="translate(0,5)"/>
  </svg>
</section>
<h1 class="abs hero-title">HAYFIELD CREST</h1>
<div class="abs hero-sub">BEDDING &amp; FEED</div>
<div class="abs learn-btn">LEARN MORE &nbsp;›</div>
<div class="abs dots"><span></span><span class="on"></span><span></span></div>

<!-- intro cards -->
<article class="abs card card-light">
  <div class="photo" role="img" aria-label="Two horses eating hay" style="background:linear-gradient(135deg,#6b5442,#b89a6e)"></div>
  <h3>BEST BEDDING &amp; FEED</h3>
  <p>Looking for the best bedding and feed for your horse, livestock or household pet look no further. We use premium locally sourced straw and hay in all of our products and are committed in providing quality products and service.</p>
</article>
<article class="abs card card-orange">
  <div class="photo" role="img" aria-label="Woman with her horse" style="background:linear-gradient(135deg,#6b4a22,#a8a048)"></div>
  <h3>ANIMAL DESERVE BEST</h3>
  <p>Your animal deserves the very best in health and comfort to keep them healthy, strong and happy. Our products are designed for horses, livestock (goats, cattle and sheep), small caged animals (rabbits, guinea pigs and more).</p>
</article>
<article class="abs card card-brown">
  <div class="photo" role="img" aria-label="Aerial view of the red farm buildings" style="background:linear-gradient(160deg,#6e7a5a,#9a4a44)"></div>
  <h3>OFFER SUPPLY &amp; DELIVERY</h3>
  <p>Hayfield Crest offers supply and delivery of fresh bedding as well as removal of waste bedding. Let us deliver you a container of fresh straw and haul your waste bedding away. A full service solution that is sustainable and responsible.</p>
</article>

<!-- benefits -->
<section class="abs benefits">
  <div class="abs benefit" style="left:110px">
    <svg width="46" height="66" viewBox="0 0 46 66" fill="none" stroke="#f7941d" stroke-width="2"><circle cx="23" cy="23" r="19"/><circle cx="23" cy="23" r="12"/><path d="M12 38 L6 62 L14 56 L18 64 L23 42 M34 38 L40 62 L32 56 L28 64 L23 42"/></svg>
    <div><h4>QUALITY<br>GUARANTEED</h4><p>Grown for quality - 100% natural with no<br>chemicals or additives</p></div>
  </div>
  <div class="abs divider" style="left:430px"></div>
  <div class="abs benefit" style="left:460px">
    <svg width="52" height="52" viewBox="0 0 52 52" fill="none" stroke="#f7941d" stroke-width="3"><path d="M8 8 A22 22 0 1 0 44 8"/><path d="M18 34 L34 18 M18 18 L34 34"/></svg>
    <div><h4>FULL SERVICE<br>SOLUTION</h4><p>Dedicated in providing a full service solution<br>of bedding supply &amp; waste removal</p></div>
  </div>
  <div class="abs divider" style="left:800px"></div>
  <div class="abs benefit" style="left:820px">
    <svg width="60" height="60" viewBox="0 0 60 60" fill="none" stroke="#f7941d" stroke-width="2"><ellipse cx="30" cy="36" rx="24" ry="16"/><circle cx="36" cy="10" r="6"/><path d="M18 50 V58 M40 50 V58"/></svg>
    <div><h4>CONVENIENT &amp; COST<br>EFFECTIVE</h4><p>Compressed bags , pellets or bulk products<br>saving in shipping costs</p></div>
  </div>
</section>

<!-- bedding -->
<h2 class="abs section-title bed-title">BEDDING</h2>
<div class="abs bed-photo" role="img" aria-label="Horse lying in straw bedding" style="background:radial-gradient(circle at 50% 45%,#8a4a22,#b89a6a 70%,#d9c394)"></div>

<svg class="abs" style="left:0;top:1640px" width="1200" height="540" viewBox="0 0 1200 540" fill="none" stroke="#b7b7b7" stroke-width="2">
  <path d="M440 100 Q410 70 388 80 M388 80 l8 -8 M388 80 l10 4"/>
  <path d="M760 100 Q790 70 820 78 M820 78 l-8 -8 M820 78 l-10 4"/>
  <path d="M432 260 Q410 288 370 290 M370 290 l8 -7 M370 290 l8 7"/>
  <path d="M772 262 Q790 290 830 292 M830 292 l-8 -7 M830 292 l-8 7"/>
  <path d="M508 368 Q490 400 446 404 M446 404 l8 -8 M446 404 l10 4"/>
  <path d="M678 370 Q700 400 740 402 M740 402 l-10 -6 M740 402 l-8 6"/>
  <path d="M600 400 V440 M600 440 l-7 -8 M600 440 l7 -8"/>
</svg>

<div class="abs bed-label" style="left:160px;top:1694px;text-align:right;width:110px">100% Natural<br>Chopped Straw</div>
<div class="abs badge o" style="left:284px;top:1674px"><svg width="34" height="34" viewBox="0 0 34 34" fill="none" stroke="#fff" stroke-width="2"><path d="M17 3 C27 12 27 24 17 31 C7 24 7 12 17 3 Z M17 8 V31"/></svg></div>

<div class="abs bed-label" style="left:202px;top:1876px;text-align:right;width:84px">Low Dust</div>
<div class="abs badge b" style="left:300px;top:1849px"><svg width="40" height="40" viewBox="0 0 40 40" fill="none" stroke="#fff" stroke-width="2"><circle cx="20" cy="20" r="15"/><path d="M9 9 L31 31"/></svg></div>

<div class="abs bed-label" style="left:230px;top:2032px;text-align:right;width:122px">Chemical &amp;<br>Additive Free</div>
<div class="abs badge o" style="left:366px;top:2018px"><svg width="40" height="40" viewBox="0 0 40 40" fill="none" stroke="#fff" stroke-width="2"><circle cx="20" cy="20" r="15"/><path d="M16 10 V18 L10 30 H30 L24 18 V10"/></svg></div>

<div class="abs badge b" style="left:562px;top:2099px"><svg width="40" height="40" viewBox="0 0 40 40" fill="none" stroke="#fff" stroke-width="2"><circle cx="14" cy="24" r="6"/><circle cx="26" cy="26" r="5"/><circle cx="22" cy="13" r="4"/></svg></div>
<div class="abs bed-label" style="left:500px;top:2184px;text-align:center;width:200px">Clean &amp; Highly<br>Absorbent</div>

<div class="abs badge o" style="left:752px;top:2018px"><svg width="44" height="30" viewBox="0 0 44 30" fill="none" stroke="#fff" stroke-width="2"><path d="M4 24 H40 L34 10 H14 Z M20 10 V4 H30"/></svg></div>
<div class="abs bed-label" style="left:838px;top:2040px;width:140px">Cheaper than<br>Wood Shavings</div>

<div class="abs badge b" style="left:816px;top:1849px"><svg width="40" height="40" viewBox="0 0 40 40" fill="none" stroke="#fff" stroke-width="2"><circle cx="20" cy="20" r="15"/><path d="M5 20 H35 M20 5 C12 14 12 26 20 35 C28 26 28 14 20 5"/></svg></div>
<div class="abs bed-label" style="left:904px;top:1872px;width:170px">Economic – less used<br>and less wasted</div>

<div class="abs badge o" style="left:842px;top:1674px"><svg width="40" height="40" viewBox="0 0 40 40" fill="none" stroke="#fff" stroke-width="2"><path d="M20 6 L32 28 H8 Z"/></svg></div>
<div class="abs bed-label" style="left:934px;top:1694px;width:200px">Environmentally Friendly –<br>Recyclable &amp; Compostable</div>

<div class="abs view-btn" style="left:505px;top:2260px;width:190px">VIEW BEDDING &nbsp;›</div>

<!-- feed -->
<svg class="abs feed" viewBox="0 0 1200 625" width="1200" height="625">
  <path d="M0 10 Q600 -10 1200 10 L1200 625 L0 625 Z" fill="#f7941d"/>
</svg>
<h2 class="abs feed-title">OUR FEED</h2>
<p class="abs feed-copy">Hay cubes and pellets are made from premium hay offering a variety of animals a feed that is non-GMO and packed with natural nutrients. These pellets and cubes are less bulky to handle, store and ship. As well, they reduce the amount of wasted feed.</p>

<div class="abs feed-item" style="left:120px;top:2656px"><svg width="24" height="30" viewBox="0 0 24 30" fill="none" stroke="#fff" stroke-width="1.6"><path d="M12 2 C20 10 20 20 12 28 C4 20 4 10 12 2 Z M12 6 V28"/></svg>100% Natural</div>
<div class="abs feed-item" style="left:292px;top:2654px"><svg width="34" height="34" viewBox="0 0 34 34" fill="none" stroke="#fff" stroke-width="1.6"><circle cx="17" cy="17" r="15"/><path d="M13 8 V15 L8 26 H26 L21 15 V8"/></svg>Chemical &amp;<br>Additive Free</div>
<div class="abs feed-item" style="left:442px;top:2654px"><svg width="36" height="34" viewBox="0 0 36 34" fill="none" stroke="#fff" stroke-width="1.6"><rect x="2" y="16" width="14" height="14"/><rect x="18" y="16" width="14" height="14"/><rect x="10" y="2" width="14" height="14"/></svg>Available in<br>Pellets or Cubes</div>

<div class="abs feed-item" style="left:114px;top:2730px"><svg width="34" height="32" viewBox="0 0 34 32" fill="none" stroke="#fff" stroke-width="1.6"><circle cx="9" cy="20" r="6"/><circle cx="22" cy="22" r="5"/><circle cx="20" cy="9" r="4"/></svg>Clean - Eliminates<br>Dust From Feeding<br>Baled Hay</div>
<div class="abs feed-item" style="left:292px;top:2726px"><svg width="30" height="34" viewBox="0 0 30 34" fill="none" stroke="#fff" stroke-width="1.6"><path d="M3 6 H27 M8 6 L10 32 H20 L22 6 M11 6 V2 H19 V6"/></svg>Eliminate Waste<br>In Feeding</div>
<div class="abs feed-item" style="left:446px;top:2730px"><svg width="34" height="28" viewBox="0 0 34 28" fill="none" stroke="#fff" stroke-width="1.6"><path d="M4 20 C10 4 24 4 30 14 C24 24 10 26 4 20 Z"/></svg>High Protein<br>Content</div>

<div class="abs feed-item" style="left:112px;top:2800px"><svg width="34" height="34" viewBox="0 0 34 34" fill="none" stroke="#fff" stroke-width="1.6"><circle cx="15" cy="15" r="12"/><path d="M24 26 L31 33"/></svg>Cost Effective</div>
<div class="abs feed-item" style="left:288px;top:2800px"><svg width="34" height="34" viewBox="0 0 34 34" fill="none" stroke="#fff" stroke-width="1.6"><circle cx="17" cy="17" r="15"/><path d="M10 17 L15 22 L25 11"/></svg>Convenient</div>
<div class="abs feed-item" style="left:446px;top:2800px"><svg width="34" height="32" viewBox="0 0 34 32" fill="none" stroke="#fff" stroke-width="1.6"><path d="M17 3 L30 27 H4 Z"/></svg>Less wasted<br>feed</div>

<div class="abs view-btn" style="left:116px;top:2866px;width:154px;height:46px">VIEW FEED &nbsp;›</div>

<div class="abs feed-photo-a" role="img" aria-label="Man feeding a horse from a metal bucket" style="background:linear-gradient(135deg,#5e4632,#a7896a 60%,#d2c1a6)"></div>
<div class="abs feed-photo-b" role="img" aria-label="Close-up of hay pellets" style="background:linear-gradient(135deg,#7a5a2a,#c4a36a)"></div>

<!-- delivery -->
<div class="abs map" role="img" aria-label="Map of Canada and the USA showing the delivery area" style="background:linear-gradient(180deg,#6b2b12 0%,#6b2b12 44%,#f39a12 44%,#f39a12 100%);border-radius:40px 60px 90px 120px"></div>
<h2 class="abs deliv-title">DELIVERY IN CANADA &amp; USA</h2>
<div class="abs deliv-copy">
  <p>Looking for the best bedding and feed for your horse, livestock or household pet look no further.</p>
  <p>We use premium locally sourced straw and hay in all of our products and are committed in providing quality products and service.</p>
</div>
<div class="abs outline-btn">CONTACT US</div>

<!-- footer -->
<svg class="abs footer" viewBox="0 0 1200 498" width="1200" height="498">
  <path d="M0 0 Q600 120 1200 0 L1200 498 L0 498 Z" fill="#3a1c0e"/>
</svg>
<div class="abs foot-brand">
  <div class="foot-dot"></div>
  <div class="foot-name">HAYFIELD CREST</div>
  <div class="foot-sub">BEDDING &amp; FEED</div>
</div>
<div class="abs socials"><span></span><span></span><span></span><span></span></div>

<div class="abs foot-col" style="left:427px;top:3640px">
  <h5>SITEMAP</h5>
  <ul><li>Home</li><li>About Us</li><li>Our Bedding</li><li>Feed</li><li>Contact Us</li></ul>
</div>
<div class="abs foot-col" style="left:602px;top:3642px">
  <h5>CONTACT US</h5>
  <div class="contact-line"><svg width="14" height="18" viewBox="0 0 14 18"><path d="M7 1 C3 1 1 4 1 7 C1 11 7 17 7 17 C7 17 13 11 13 7 C13 4 11 1 7 1 Z" fill="#f7941d"/><circle cx="7" cy="7" r="2.4" fill="#3a1c0e"/></svg><span>123 Avenue name, City name<br>25252, United States</span></div>
  <div class="contact-line" style="margin-top:2px"><svg width="14" height="16" viewBox="0 0 14 16"><path d="M3 1 L6 5 L4 7 C5 10 7 12 9 12 L11 10 L13 13 L11 15 C5 14 1 9 1 3 Z" fill="#f7941d"/></svg><span>(825) 555-0142</span></div>
  <div class="contact-line" style="margin-top:12px"><svg width="16" height="14" viewBox="0 0 16 14"><rect x="1" y="2" width="14" height="10" fill="#f7941d"/><path d="M1 2 L8 8 L15 2" fill="none" stroke="#3a1c0e" stroke-width="1.2"/></svg><span>hello@hayfieldcrest.com</span></div>
</div>
<div class="abs foot-col" style="left:864px;top:3640px"><h5>NEWSLETTER SIGN UP</h5></div>
<div class="abs email-field">Email address</div>
<div class="abs sub-btn">SUBSCRIBE</div>
<div class="abs copyright">© Copyright 2020 . Hayfield Crest . All Right Reserved</div>

</body>
</html>
```